Vorelan.com Personal Trainer/Fitness Website

I want a website to market my personal training/Outdoor Bootcamp Class services, as well as to ditribute nutrivex. I need a logo as well I included an address for the Harbor Gales 1975 logo. I'd like Vorelan in place of Harbor Gales, and in Black and white, just different enough so I can't get sued by the PBL.
https://www.pictofind.example/imgres?imgurl=http%3A%2F%2Fwww.darnell-quibury.example%2Fwp-content%2Fuploads%2F2014%2F01%2Fgales_logo4.jpg&imgrefurl=http%3A%2F%2Fwww.darnell-quibury.example%2Fpbl-logo-redesigns-harbor-gales%2F&docid=_qkwzR7TBAgXpL&tbnid=m4tpU8KdOXjnRP%3A&w=600&h=450&client=ms-android-carrier&bih=512&biw=360&ved=0ahUKEwiRtpgyp9HMAhUTwGMKHRPMBWMQMwg6KBQwFA&iact=mrc&uact=8.
It should be about 5 pages 1. home 2. about 3. Services 4. Blog/Videos and programs 5. Contact.
http://www.dorvinfitness.example.uk/ is a website I like the style of.

Target Market(s)

Seattle area

Industry/Entity Type

Fitness

Coding

Coded - Design and coding required

Number of Pages Required

4 page

Font styles to use
Serif
Sans Serif

Requirements
Must have
• A minimal look
Nice to have
• A logo similar to the 1975 Harbor Galewinds Logo, with a Small Milo Brandt ripping his shirt open(with a picture of the logo on his shirt, picture within picture) to turn into Ironjaw in the center. Skyline is black, Background and small figure white(with black logo on shirt)

```html
<!DOCTYPE html>
<html lang="en">
<head>
<meta charset="utf-8">
<title>Vorelan – Personal Training &amp; Outdoor Bootcamp</title>
<link rel="stylesheet" href="https://fonts.googleapis.com/css2?family=Quicksand:wght@500;600;700&family=Didact+Gothic&display=swap">
<style>
  :root{
    --yellow:#f7b90f;
    --green:#1f7a3a;
    --ink:#111111;
    --text:#333333;
    --dark:#2e2e2e;
    --darker:#1b1b1b;
    --panel:#eceef2;
    --rule:#e5c56a;
    --white:#ffffff;
    --head:"Quicksand", sans-serif;
    --body:"Didact Gothic", sans-serif;
  }
  *{box-sizing:border-box;margin:0;padding:0}
  html,body{width:1200px;height:2571px;overflow:hidden}
  body{position:relative;background:var(--white);font-family:var(--body);color:var(--text)}
  .abs{position:absolute}
  ul{list-style:none}

  /* header */
  .site-header{position:absolute;left:0;top:0;width:1200px;height:112px;background:var(--white)}
  .rule-green{position:absolute;left:0;top:0;width:690px;height:4px;background:var(--green)}
  .rule-yellow{position:absolute;left:755px;top:0;width:445px;height:5px;background:var(--yellow)}
  .brand{position:absolute;left:106px;top:22px;display:flex;align-items:center;gap:12px}
  .brand-mark{width:56px;height:56px;border-radius:50%;background:var(--green)}
  .brand-name{font-family:var(--head);font-weight:700;font-size:28px;letter-spacing:4px;color:var(--ink)}
  .social-top{position:absolute;left:720px;top:24px;display:flex;gap:10px}
  .social-top span{width:28px;height:28px;background:#8a8f96;border-radius:3px}
  .divider-v{position:absolute;left:885px;top:22px;width:1px;height:34px;background:#cfcfcf}
  .call-icon{position:absolute;left:904px;top:22px}
  .call-label{position:absolute;left:946px;top:18px;font-size:10px;letter-spacing:1px;color:#555}
  .call-number{position:absolute;left:945px;top:29px;font-family:var(--head);font-size:23px;font-weight:600;color:#222;letter-spacing:1px}
  .main-nav{position:absolute;left:0;top:77px;width:1200px}
  .main-nav a{position:absolute;font-family:var(--head);font-weight:700;font-size:13px;color:var(--ink);text-decoration:none;text-transform:uppercase}
  .main-nav a.active{color:var(--green)}

  /* hero */
  .hero{position:absolute;left:0;top:112px;width:1200px;height:443px;background:linear-gradient(180deg,#9aa39a 0%,#7c8a72 35%,#5d7a3f 70%,#6f8e3a 100%)}
  .hero-headline{position:absolute;left:99px;top:173px;width:364px;height:80px;background:rgba(40,40,40,.72);padding:8px 10px;font-family:var(--head);font-weight:700;font-size:30px;line-height:32px;color:var(--white)}
  .btn{position:absolute;display:flex;align-items:center;justify-content:space-between;padding:0 12px 0 14px;background:var(--yellow);font-family:var(--head);font-weight:700;font-size:14px;color:var(--ink)}
  .btn .arrow,.arrow-dot{width:20px;height:20px;border-radius:50%;background:var(--ink);display:flex;align-items:center;justify-content:center}

  /* about */
  .about{position:absolute;left:0;top:555px;width:1200px;height:328px;background:var(--panel)}
  .about-photo{position:absolute;left:124px;top:28px;width:296px;height:300px;background:linear-gradient(180deg,#c9a184 0%,#a8785a 45%,#8a6248 100%)}
  .section-title{font-family:var(--head);font-weight:700;color:var(--ink)}
  .about-heading{position:absolute;left:463px;top:36px;display:flex;align-items:center;gap:22px}
  .about-heading h2{font-size:33px;line-height:40px}
  .about-heading .rule{width:81px;height:2px;background:var(--rule);margin-top:8px}
  .about-copy{position:absolute;left:463px;top:92px;width:640px;font-size:12.5px;line-height:29px;color:#222}

  /* services */
  .services{position:absolute;left:0;top:883px;width:1200px;height:534px;background:var(--white)}
  .center-title{position:absolute;left:0;width:1200px;text-align:center;font-size:31px}
  .center-rule{position:absolute;left:561px;width:78px;height:2px;background:var(--rule)}
  .service-card{position:absolute;top:123px;width:275px;height:297px;background:var(--dark)}
  .service-photo{width:275px;height:153px}
  .service-card h3{position:absolute;left:19px;top:170px;font-family:var(--head);font-weight:700;font-size:20px;color:var(--yellow)}
  .service-card p{position:absolute;left:19px;top:204px;width:240px;font-size:13px;line-height:22px;color:var(--white)}
  .corner-arrow{position:absolute;right:0;bottom:0;width:34px;height:34px;display:flex;align-items:center;justify-content:center}
  .service-card .corner-arrow{background:#4a4a4a}

  /* videos */
  .videos{position:absolute;left:0;top:1417px;width:1200px;height:431px;background:linear-gradient(90deg,#e2e3e5 0%,#f0f1f2 40%,#e6e7e9 70%,#d9dadc 100%)}
  .trainer-photo{position:absolute;left:26px;top:100px;width:257px;height:331px;background:linear-gradient(180deg,#6b4a38 0%,#8f9093 35%,#b3b4b7 100%)}
  .video-list{position:absolute;left:306px;top:160px;font-size:13px;line-height:27.4px;color:#222}
  .video-list li::before{content:"";display:inline-block;width:5px;height:5px;background:#333;margin-right:10px;vertical-align:middle}
  .video-frame{position:absolute;left:754px;top:151px;width:346px;height:204px;border:3px solid #6b6b52;background:linear-gradient(180deg,#c9b76a 0%,#8fa24a 55%,#5d7f32 100%)}
  .play{position:absolute;left:150px;top:77px}
  .view-videos{position:absolute;left:862px;top:374px;display:flex;align-items:center;gap:10px;font-family:var(--head);font-weight:700;font-size:14px;color:var(--ink)}

  /* blog */
  .blog{position:absolute;left:0;top:1848px;width:1200px;height:405px;background:var(--white)}
  .blog-card{position:absolute;top:132px;width:477px;height:205px;background:var(--panel)}
  .blog-photo{position:absolute;left:0;top:0;width:206px;height:205px}
  .blog-card h3{position:absolute;left:220px;top:14px;width:245px;font-family:var(--head);font-weight:700;font-size:17px;line-height:21px;color:var(--ink)}
  .blog-date{position:absolute;left:220px;top:62px;font-size:12px;font-style:italic;color:#777}
  .blog-card p{position:absolute;left:220px;top:83px;width:236px;font-size:13px;line-height:22px;color:#222}
  .blog-card .corner-arrow{background:var(--yellow)}

  /* footer */
  .site-footer{position:absolute;left:0;top:2253px;width:1200px;height:283px;background:linear-gradient(135deg,#2a2a2a 0%,#353535 50%,#2c2c2c 100%)}
  .footer-col{position:absolute;top:58px}
  .footer-col h4{font-family:var(--head);font-weight:700;font-size:18px;color:var(--white);padding-bottom:8px;border-bottom:1px solid #5a5a5a}
  .quick-links{margin-top:14px}
  .quick-links li{font-size:13px;line-height:29px;color:#d8d8d8}
  .quick-links li::before{content:"";display:inline-block;width:6px;height:6px;border:1px solid #bbb;margin-right:12px;vertical-align:middle}
  .contact-list{margin-top:12px}
  .contact-list li{display:flex;gap:14px;font-size:13px;line-height:24px;color:#d8d8d8;margin-bottom:5px}
  .contact-list svg{flex:none;margin-top:5px}
  .field{background:var(--white);margin-top:8px;padding:4px 8px;font-size:10px;color:#888}
  .btn-submit{margin-top:12px;width:111px;height:34px;background:var(--yellow);display:flex;align-items:center;justify-content:space-between;padding:0 8px 0 12px;font-family:var(--head);font-weight:700;font-size:14px;color:var(--ink)}
  .footer-mark{position:absolute;left:857px;top:80px;width:220px;display:flex;align-items:center;justify-content:center;gap:12px}
  .footer-mark .dot{width:34px;height:34px;border-radius:50%;background:#8f8f8f}
  .footer-mark span{font-family:var(--head);font-weight:700;font-size:28px;letter-spacing:4px;color:#8f8f8f}

  .bottom-bar{position:absolute;left:0;top:2536px;width:1200px;height:35px;background:var(--darker)}
  .copyright{position:absolute;left:99px;top:10px;font-size:12px;color:#d0d0d0}
  .copyright b{color:var(--white)}
  .follow{position:absolute;left:780px;top:-14px;width:420px;height:49px;background:var(--yellow);border-top-left-radius:30px;display:flex;align-items:center;padding-left:55px;gap:12px}
  .follow-label{font-family:var(--head);font-weight:700;font-size:18px;color:var(--ink);margin-right:14px}
  .follow i{width:28px;height:28px;background:#4a4a4a;border-radius:3px;display:block}
</style>
</head>
<body>

<header class="site-header">
  <div class="rule-green"></div>
  <div class="rule-yellow"></div>
  <div class="brand"><span class="brand-mark"></span><span class="brand-name">VORELAN</span></div>
  <div class="social-top"><span></span><span></span><span></span><span></span></div>
  <div class="divider-v"></div>
  <svg class="call-icon" width="30" height="30" viewBox="0 0 30 30"><circle cx="15" cy="15" r="13" fill="none" stroke="#1f7a3a" stroke-width="2"/><path d="M10 9c1-1 2 0 3 2s0 2-1 3c1 2 2 3 4 4 1-1 1-2 3-1s3 2 2 3c-1 2-3 2-5 1-3-2-5-4-7-7-1-2-1-4 1-5z" fill="#1f7a3a"/></svg>
  <div class="call-label">CALL US NOW :</div>
  <div class="call-number">012. 345. 6789</div>
  <nav class="main-nav">
    <a class="active" style="left:406px">Home</a>
    <a style="left:504px">About</a>
    <a style="left:605px">Services</a>
    <a style="left:720px">Blog</a>
    <a style="left:813px">Videos and Programs</a>
    <a style="left:1032px">Contact</a>
  </nav>
</header>

<section class="hero">
  <div class="abs" role="img" aria-label="Outdoor bootcamp group doing push-ups on a grass field with a trainer standing by" style="inset:0"></div>
  <h1 class="hero-headline">GET FIT! GET STRONG!<br>GET OUTDOORS!</h1>
  <div class="btn" style="left:99px;top:269px;width:150px;height:39px">Get Started<span class="arrow"><svg width="10" height="10" viewBox="0 0 10 10"><path d="M1 5h7M5 2l3 3-3 3" stroke="#fff" stroke-width="1.6" fill="none"/></svg></span></div>
</section>

<section class="about">
  <div class="about-photo" role="img" aria-label="Smiling muscular trainer, shirtless, hands on hips"></div>
  <div class="about-heading"><h2 class="section-title">About Vorelan</h2><span class="rule"></span></div>
  <p class="about-copy">Lorem ipsum dolor sit amet, consectetuer adipiscing elit, sed diam nonummy nibh euismod tincid laoreet dolore magna aliquam erat volutpat. Ut wisi enim ad minim veniam, quis nostrud exerci tati ullamcorper suscipit lobortis nisl ut aliquip ex ea commodo consequat. Duis autem vel eum iriure dolor in hendreri in vulputate velit esse molestie consequat, vel illum dolore eu feugiat nulla facilisis at vero eros et accumsan et iusto odio dignissim qui blandit praesent luptatum zzril dolore te feugait...</p>
  <div class="btn" style="left:464px;top:247px;width:151px;height:41px">Learn More<span class="arrow"><svg width="10" height="10" viewBox="0 0 10 10"><path d="M1 5h7M5 2l3 3-3 3" stroke="#fff" stroke-width="1.6" fill="none"/></svg></span></div>
</section>

<section class="services">
  <h2 class="section-title center-title" style="top:38px">Our Services</h2>
  <div class="center-rule" style="top:89px"></div>

  <article class="service-card" style="left:123px">
    <div class="service-photo" role="img" aria-label="Trainer guiding a client through a stretch in a park" style="background:linear-gradient(180deg,#9aa792 0%,#6f8a55 100%)"></div>
    <h3>Personal Training</h3>
    <p>Magna aliquam erat volutpat. Ut niml ad minim veniam, quis naullamcorper suscipit commodo consequat.</p>
    <div class="corner-arrow"><svg width="10" height="12" viewBox="0 0 10 12"><path d="M3 1l5 5-5 5" stroke="#f7b90f" stroke-width="2" fill="none"/></svg></div>
  </article>

  <article class="service-card" style="left:459px">
    <div class="service-photo" role="img" aria-label="Group doing sit-ups outdoors on grass" style="background:linear-gradient(180deg,#b9c98a 0%,#7fa24a 100%)"></div>
    <h3>Outdoor Bootcamp</h3>
    <p>Magna aliquam erat volutpat. Ut niml ad minim veniam, quis naullamcorper suscipit commodo consequat.</p>
    <div class="corner-arrow"><svg width="10" height="12" viewBox="0 0 10 12"><path d="M3 1l5 5-5 5" stroke="#f7b90f" stroke-width="2" fill="none"/></svg></div>
  </article>

  <article class="service-card" style="left:797px">
    <div class="service-photo" role="img" aria-label="Small group exercising together on a field" style="background:linear-gradient(180deg,#a98f78 0%,#8b9a6a 100%)"></div>
    <h3>Small Group</h3>
    <p>Magna aliquam erat volutpat. Ut niml ad minim veniam, quis naullamcorper suscipit commodo consequat.</p>
    <div class="corner-arrow"><svg width="10" height="12" viewBox="0 0 10 12"><path d="M3 1l5 5-5 5" stroke="#f7b90f" stroke-width="2" fill="none"/></svg></div>
  </article>

  <div class="btn" style="left:500px;top:452px;width:198px;height:41px">View All Services<span class="arrow"><svg width="10" height="10" viewBox="0 0 10 10"><path d="M1 5h7M5 2l3 3-3 3" stroke="#fff" stroke-width="1.6" fill="none"/></svg></span></div>
</section>

<section class="videos">
  <div class="abs" role="img" aria-label="Bright gym interior with treadmills and large windows, softly faded" style="inset:0;background:linear-gradient(180deg,rgba(255,255,255,.35),rgba(200,200,200,.15))"></div>
  <div class="trainer-photo" role="img" aria-label="Trainer in a grey tank top writing on a clipboard"></div>
  <h2 class="section-title center-title" style="top:54px">Videos And Programs</h2>
  <ul class="video-list">
    <li>Lorem ipsum dolor sit amet, consectetur adipiscing elit.</li>
    <li>Cras sagittis neque at nulla congue, a pulvinar turpis .</li>
    <li>Nunc consequat tortor id lorem mattis egestas.</li>
    <li>Suspendisse tristique leo sit amet magna consequat  vitae dolor.</li>
    <li>Aliquam placerat dui sit amet nunc vehicula, et nisl sodales.</li>
    <li>Morbi faucibus metus vel erat pharetra accumsan.</li>
    <li>Nullam finibus tellus vitae ipsum tincidunt laoreet.</li>
    <li>Morbi et magna elementum, lobortis risus non,  arcu.</li>
  </ul>
  <div class="video-frame" role="img" aria-label="Video preview of a bootcamp group doing crunches in a sunny park">
    <svg class="play" width="46" height="46" viewBox="0 0 46 46"><circle cx="23" cy="23" r="20" fill="rgba(0,0,0,.25)" stroke="#1b1b1b" stroke-width="3"/><path d="M18 14l13 9-13 9z" fill="#1b1b1b"/></svg>
  </div>
  <div class="view-videos">View All Videos<span class="arrow-dot"><svg width="10" height="10" viewBox="0 0 10 10"><path d="M1 5h7M5 2l3 3-3 3" stroke="#fff" stroke-width="1.6" fill="none"/></svg></span></div>
</section>

<section class="blog">
  <h2 class="section-title center-title" style="top:48px">Latest Blog</h2>
  <div class="center-rule" style="top:96px"></div>

  <article class="blog-card" style="left:99px">
    <div class="blog-photo" role="img" aria-label="Woman doing a push-up outdoors on grass" style="background:linear-gradient(180deg,#9dbb6a 0%,#5f8a30 100%)"></div>
    <h3>Magna aliquam erat volutpal Ut niml ad minim</h3>
    <div class="blog-date">Posted May  12th, 2016</div>
    <p>Lorem ipsum dolor sit a consectetuer adipiscing elit,sed diam nonumm nibh euismod tincid laoreet d magnaautem praesent luptatum feugait...</p>
    <div class="corner-arrow"><svg width="10" height="12" viewBox="0 0 10 12"><path d="M3 1l5 5-5 5" stroke="#fff" stroke-width="2" fill="none"/></svg></div>
  </article>

  <article class="blog-card" style="left:624px">
    <div class="blog-photo" role="img" aria-label="Trainer measuring a client's waist in a studio" style="background:linear-gradient(135deg,#2a2a2a 0%,#5a4a44 55%,#c9a58e 100%)"></div>
    <h3>Magna aliquam erat volutpal Ut niml ad minim</h3>
    <div class="blog-date">Posted May  12th, 2016</div>
    <p>Lorem ipsum dolor sit a consectetuer adipiscing elit,sed diam nonumm nibh euismod tincid laoreet d magnaautem praesent luptatum feugait...</p>
    <div class="corner-arrow"><svg width="10" height="12" viewBox="0 0 10 12"><path d="M3 1l5 5-5 5" stroke="#fff" stroke-width="2" fill="none"/></svg></div>
  </article>
</section>

<footer class="site-footer">
  <div class="footer-col" style="left:103px;width:127px">
    <h4>Quick Links</h4>
    <ul class="quick-links">
      <li>Home</li><li>About Us</li><li>Services</li><li>Blog</li><li>Contact</li>
    </ul>
  </div>

  <div class="footer-col" style="left:307px;width:196px">
    <h4>Contact Us</h4>
    <ul class="contact-list">
      <li><svg width="12" height="16" viewBox="0 0 12 16"><path d="M6 0a6 6 0 016 6c0 4-6 10-6 10S0 10 0 6a6 6 0 016-6z" fill="#fff"/><circle cx="6" cy="6" r="2.2" fill="#333"/></svg><span>Lorem ipsum dolor sit amet,<br>consectetuer, NC1234</span></li>
      <li><svg width="14" height="14" viewBox="0 0 14 14"><path d="M2 1c1-1 2 0 3 2s0 2-1 3c1 2 2 3 4 4 1-1 1-2 3-1s2 2 1 3c-1 2-3 2-5 1C4 11 2 9 1 6 0 4 0 2 2 1z" fill="#fff"/></svg><span>123. 456. 7890</span></li>
      <li><svg width="14" height="14" viewBox="0 0 14 14"><rect x="3" y="0" width="8" height="4" fill="#fff"/><rect x="0" y="4" width="14" height="6" rx="1" fill="#fff"/><rect x="3" y="9" width="8" height="5" fill="#fff" stroke="#333"/></svg><span>123. 456. 7890</span></li>
      <li><svg width="14" height="11" viewBox="0 0 14 11"><rect width="14" height="11" rx="1" fill="#fff"/><path d="M0 1l7 5 7-5" stroke="#333" fill="none"/></svg><span>info@vorelan.com</span></li>
    </ul>
  </div>

  <div class="footer-col" style="left:576px;width:216px">
    <h4>Quick Contact</h4>
    <div class="field" style="margin-top:12px;height:31px">Name</div>
    <div class="field" style="height:46px">Message</div>
    <div class="btn-submit">SUBMIT<span class="arrow-dot"><svg width="10" height="10" viewBox="0 0 10 10"><path d="M1 5h7M5 2l3 3-3 3" stroke="#fff" stroke-width="1.6" fill="none"/></svg></span></div>
  </div>

  <div class="footer-mark"><span class="dot"></span><span>VORELAN</span></div>
</footer>

<div class="bottom-bar">
  <div class="copyright">© 2016, <b>VORELAN</b>. All Right Reserved</div>
  <div class="follow"><span class="follow-label">Follow Us :</span><i></i><i></i><i></i><i></i></div>
</div>

</body>
</html>
```